Revamp my web site design

Willowbank Care Practitioners is a not for profit organisation focused on providing emotional support and counselling services to those with cancer or affected by cancer including those bereaved.

Our web site is intended to welcome suffers to engage with the services of its members and is also provided to encourage additional counsellors to join the organisation and then supports its members with access to materials and courses to extend their professional development.

We have a limited budget and seek to not only improve the attractiveness of the site but also improve the functionality and ease of maintenance. Especially site administrtaion should allow for uploading documents, adding new members, news and events easily.

Existing site is www.willowbankcare.com.au

```html
<!DOCTYPE html>
<html lang="en">
<head>
<meta charset="utf-8">
<title>Willowbank Care Practitioners Inc</title>
<link href="https://fonts.googleapis.com/css2?family=Roboto+Condensed:wght@400;500&family=Roboto:wght@400;500&display=swap" rel="stylesheet">
<style>
:root{
  --green:#5b8a12;
  --green-dark:#4d7a0c;
  --orange:#e8642c;
  --ink:#1a1a1a;
  --nav:#555;
  --body:#555;
  --rule:#e2e2e2;
  --footer:#000;
  --white:#fff;
}
*{margin:0;padding:0;box-sizing:border-box}
html,body{width:1200px;height:1160px;overflow:hidden;background:var(--white)}
body{font-family:"Roboto",Arial,sans-serif;color:var(--body);position:relative}
.wrap{position:absolute;left:119px;width:961px}

.site-header{position:absolute;top:0;left:0;width:1200px;height:89px}
.brand{position:absolute;left:119px;top:24px;display:flex;align-items:center;gap:14px}
.brand-dot{width:28px;height:28px;border-radius:50%;background:var(--green)}
.brand-name{font-family:"Roboto Condensed",sans-serif;font-size:18px;line-height:21px;color:var(--green);text-transform:uppercase;width:180px}
.main-nav{position:absolute;right:121px;top:38px;display:flex;gap:32px;font-family:"Roboto Condensed",sans-serif;font-size:13px;font-weight:500}
.main-nav a{color:var(--nav);text-decoration:none;text-transform:uppercase}
.main-nav a.active{color:var(--green)}

.hero{position:absolute;top:89px;left:0;width:1200px;height:399px;
  background:linear-gradient(90deg,#5a4032 0%,#8a6a56 18%,#d8dde6 40%,#e8ecf2 60%,#eed7c6 80%,#c9c6c8 100%);
  border-bottom:2px solid #ddd}
.dots{position:absolute;left:578px;top:377px;display:flex;gap:10px;align-items:center}
.dots i{width:8px;height:8px;border-radius:50%;background:#111;display:block}
.dots i.on{width:12px;height:12px;background:#fff;border:3px solid #e5a823}

h2{font-family:"Roboto Condensed",sans-serif;font-weight:400;font-size:21px;color:var(--ink)}
h2 span{color:var(--green)}
.photo{display:block}
p{font-size:11.5px;line-height:15px}
.btn{display:inline-block;background:var(--green);color:var(--white);font-family:"Roboto Condensed",sans-serif;font-size:12px;font-weight:500;padding:0 6px;height:28px;line-height:28px;border:1px solid #fff;outline:1px solid var(--green-dark);text-decoration:none;letter-spacing:.2px}

.welcome{position:absolute;left:119px;top:504px;width:640px}
.welcome .photo{position:absolute;left:0;top:46px;width:250px;height:180px;background:radial-gradient(circle at 50% 55%,#f4e7dd 0,#d59a78 35%,#a24b22 80%)}
.welcome .text{position:absolute;left:260px;top:46px;width:378px}
.welcome .text p{margin-bottom:15px;text-align:justify}
.welcome .btn{position:absolute;left:1px;top:247px}

.finder{position:absolute;left:779px;top:504px;width:301px}
.finder .photo{position:absolute;left:0;top:46px;width:300px;height:120px;background:linear-gradient(90deg,#e9e6e0,#c9c2b5 45%,#9d8a72 70%,#c8b99c)}
.finder p{position:absolute;top:170px;width:300px;text-align:justify;line-height:14px}
.finder .btn{position:absolute;left:1px;top:247px}

.divider{position:absolute;left:119px;top:800px;width:961px;height:1px;background:var(--rule)}

.column{position:absolute;top:821px;width:301px}
.column h2{margin-bottom:22px}
.item{display:flex;gap:10px;height:100px}
.item .photo{width:80px;height:80px;flex:none}
.item h3{font-size:12px;font-weight:500;color:var(--green);line-height:14px}
.item time{display:block;font-size:12px;line-height:20px}
.item p{text-align:justify;line-height:14px}
.column .btn{margin-top:1px;margin-left:1px}

.site-footer{position:absolute;top:1118px;left:0;width:1200px;height:42px;background:var(--footer);color:var(--white);font-size:11.5px}
.site-footer .legal{position:absolute;left:121px;top:13px}
.site-footer .legal a{color:var(--white);text-decoration:none}
.social{position:absolute;left:916px;top:6px;display:flex;gap:7px}
.social a{width:28px;height:28px;display:block}
</style>
</head>
<body>

<header class="site-header">
  <div class="brand">
    <span class="brand-dot"></span>
    <span class="brand-name">Willowbank Care Practitioners Inc</span>
  </div>
  <nav class="main-nav">
    <a class="active" href="#">Home</a>
    <a href="#">News</a>
    <a href="#">Events</a>
    <a href="#">Articles</a>
    <a href="#">Find a Counsellor</a>
    <a href="#">Members</a>
    <a href="#">Contact Us</a>
  </nav>
</header>

<section class="hero" role="img" aria-label="Photo of a counsellor listening attentively to a client in a clinic room">
  <div class="dots"><i></i><i class="on"></i><i></i><i></i></div>
</section>

<section class="welcome">
  <h2>Welcome to <span>Willowbank Care Practitioners&nbsp; Inc !</span></h2>
  <div class="photo" role="img" aria-label="Photo of a smiling woman making a heart shape with her hands"></div>
  <div class="text">
    <p>A diagnosis of cancer is a devastating experience for most people.</p>
    <p>Many people can get support by talking to close family or friends. However, it can sometimes help to talk to someone from outside of that circle who has been trained to listen and help you explore your feelings. You may feel as if you are riding an emotional rollercoaster. Often talking of your distress to those close to you can be difficult and painful.</p>
    <p>When someone is diagnosed with cancer, they and their family can feel shocked, numb, directionless and afraid. They often feel they need to talk things through in confidence with someone who understands the emotional challenges of cancer.</p>
  </div>
  <a class="btn" href="#">READ MORE</a>
</section>

<section class="finder">
  <h2>Find A Counsellor</h2>
  <div class="photo" role="img" aria-label="Photo of a counsellor in session with a young woman"></div>
  <p>The association provides face-to-face counselling for anyone affected by cancer, including families and friends.Each client is offered 60-minute sessions with the same counsellor,...</p>
  <a class="btn" href="#">READ MORE</a>
</section>

<div class="divider"></div>

<section class="column" style="left:119px">
  <h2>Latest News</h2>
  <article class="item"><div class="photo" role="img" aria-label="Photo of a young woman in conversation" style="background:linear-gradient(135deg,#c9b9a3,#7b6a55)"></div><div><h3>Lorem ipsum dolor sit amet, conn</h3><time>05 august, 2013</time><p>The association provides face-to-face counselling for anyone affected by cancer,</p></div></article>
  <article class="item"><div class="photo" role="img" aria-label="Photo of a woman wearing a red scarf" style="background:linear-gradient(135deg,#c7b4a5,#b62633)"></div><div><h3>Lorem ipsum dolor sit amet, conn</h3><time>05 august, 2013</time><p>The association provides face-to-face counselling for anyone affected by cancer,</p></div></article>
  <a class="btn" href="#">READ MORE</a>
</section>

<section class="column" style="left:449px">
  <h2>Latest Article</h2>
  <article class="item"><div class="photo" role="img" aria-label="Photo portrait of a young man" style="background:linear-gradient(135deg,#d8c2b0,#8e5b44)"></div><div><h3>Lorem ipsum dolor sit amet, conn</h3><time>05 august, 2013</time><p>The association provides face-to-face counselling for anyone affected by cancer,</p></div></article>
  <article class="item"><div class="photo" role="img" aria-label="Photo of a doctor meeting with a patient" style="background:linear-gradient(135deg,#f0efee,#b9a797)"></div><div><h3>Lorem ipsum dolor sit amet, conn</h3><time>05 august, 2013</time><p>The association provides face-to-face counselling for anyone affected by cancer,</p></div></article>
  <a class="btn" href="#">READ MORE</a>
</section>

<section class="column" style="left:779px">
  <h2>Upcoming Events</h2>
  <article class="item"><div class="photo" role="img" aria-label="Photo of a group counselling session" style="background:linear-gradient(135deg,#dcd6c5,#6d5a47)"></div><div><h3>Lorem ipsum dolor sit amet, conn</h3><time>05 august, 2013</time><p>The association provides face-to-face counselling for anyone affected by cancer,</p></div></article>
  <article class="item"><div class="photo" role="img" aria-label="Photo of hands held in support" style="background:linear-gradient(135deg,#b9907b,#4a2c22)"></div><div><h3>Lorem ipsum dolor sit amet, conn</h3><time>05 august, 2013</time><p>The association provides face-to-face counselling for anyone affected by cancer,</p></div></article>
  <a class="btn" href="#">READ MORE</a>
</section>

<footer class="site-footer">
  <div class="legal">© 2012&nbsp; Willowbank Care Practitioners Inc| <a href="#">Privacy Policy</a> | <a href="#">Terms</a></div>
  <div class="social">
    <a href="#" aria-label="Social link" style="background:#3b5a9a"></a>
    <a href="#" aria-label="Social link" style="background:#2ea3e0"></a>
    <a href="#" aria-label="Feed link" style="background:#f08c1e"></a>
    <a href="#" aria-label="Video link" style="background:#d9231d"></a>
    <a href="#" aria-label="Social link" style="background:#3a3a3a"></a>
  </div>
</footer>

</body>
</html>
```